Tovimar Community Development Planning New web site

Design a new web site. I have a budget of $1,500.00.
Attached on PowerPoint is a complete site plan. Home page and linked pages.
10 - 12 pages. All copy and photos will be supplied. (300dpi)
I have shown them the concept which they like.
No data bases required. Home page with animations dissolving.
They former web site has been taken down. They have been in business 30 years in New Jersey
Colors teal blues and greens
There will be a new logo)being designed)
The text in home page copy will give you a detailed story what they are all about.

files have been approved for Tovimar, Inc.   Brenton is the designer

```html
<!DOCTYPE html>
<html lang="en">
<head>
<meta charset="utf-8">
<title>Tovimar — Community Development</title>
<link rel="stylesheet" href="https://fonts.googleapis.com/css2?family=Source+Sans+3:wght@300;400;600;700&display=swap">
<style>
  :root {
    --header-bg: #253038;
    --brand-green: #6bd24f;
    --white: #ffffff;
    --section-bg: #f7f7f7;
    --heading: #5f5f5f;
    --body-text: #7a7a7a;
    --rule: #cfcfcf;
    --tagline-text: #555555;
  }
  * { box-sizing: border-box; margin: 0; padding: 0; }
  html, body { width: 1200px; height: 882px; overflow: hidden; }
  body {
    font-family: "Source Sans 3", "Source Sans Pro", Arial, sans-serif;
    background: var(--section-bg);
    position: relative;
  }

  .site-header {
    position: absolute; top: 0; left: 0;
    width: 1200px; height: 103px;
    background: var(--header-bg);
  }
  .brand {
    position: absolute; left: 75px; top: 34px;
    display: flex; align-items: center; gap: 8px;
    color: var(--brand-green);
    font-weight: 700; font-size: 28px; letter-spacing: 1.5px;
    text-transform: uppercase; line-height: 1;
  }
  .main-nav a {
    position: absolute; top: 44px;
    color: var(--white);
    font-size: 11.5px; font-weight: 600;
    text-decoration: none; text-transform: uppercase;
    letter-spacing: 0.2px; line-height: 13px;
  }
  .main-nav a.is-active {
    top: 38px; left: 374px; width: 90px; height: 25px;
    background: var(--white); color: var(--brand-green);
    border-radius: 2px; text-align: center; line-height: 25px;
    font-weight: 400;
  }
  .main-nav a.is-active::after {
    content: ""; position: absolute; left: 41px; bottom: -5px;
    border-left: 5px solid transparent; border-right: 5px solid transparent;
    border-top: 5px solid var(--white);
  }

  .hero {
    position: absolute; top: 103px; left: 0;
    width: 1200px; height: 515px;
  }
  .hero-photo {
    position: absolute; inset: 0;
    background: linear-gradient(180deg, #8fb2d4 0%, #b9cde0 30%, #d9dcdc 52%, #a8a9a6 72%, #6f8a4e 88%, #5e7d3b 100%);
  }
  .hero-kicker {
    position: absolute; left: 150px; top: 69px;
    width: 393px; height: 47px;
    background: var(--brand-green); color: var(--white);
    font-size: 21px; font-weight: 600;
    padding-left: 18px; line-height: 47px;
  }
  .hero-tagline {
    position: absolute; left: 150px; top: 127px;
    width: 365px; height: 47px;
    background: var(--white); color: var(--tagline-text);
    font-size: 21.5px; font-weight: 300;
    padding-left: 18px; line-height: 47px;
  }

  .intro {
    position: absolute; top: 618px; left: 0;
    width: 1200px; height: 262px;
    text-align: center;
    border-bottom: 1px solid #e3e3e3;
  }
  .intro-title {
    margin-top: 41px;
    color: var(--heading);
    font-size: 27px; font-weight: 700; line-height: 34px;
  }
  .intro-rule {
    width: 38px; height: 1px; background: var(--rule);
    margin: 16px auto 18px; border: 0;
  }
  .intro-text {
    color: var(--body-text);
    font-size: 19.5px; font-weight: 300; line-height: 28px;
  }
  .btn-primary {
    display: inline-block; margin-top: 21px;
    width: 138px; height: 36px; line-height: 36px;
    background: var(--brand-green); color: var(--white);
    font-size: 14px; font-weight: 700; text-decoration: none;
  }
</style>
</head>
<body>
  <header class="site-header">
    <div class="brand">Tovimar</div>
    <nav class="main-nav">
      <a class="is-active" href="#">Home</a>
      <a href="#" style="left:491px">Our Company</a>
      <a href="#" style="left:603px">Services</a>
      <a href="#" style="left:683px">Housing Rehab Application</a>
      <a href="#" style="left:874px">Affordable Application</a>
      <a href="#" style="left:1058px">Contact Us</a>
    </nav>
  </header>

  <section class="hero">
    <div class="hero-photo" role="img" aria-label="Row of restored Victorian houses with porches, a lawn and iron fence under a blue sky"></div>
    <h1 class="hero-kicker">Brookvale Community Members</h1>
    <p class="hero-tagline">Apply today for your rehab grant!</p>
  </section>

  <section class="intro">
    <h2 class="intro-title">We help communities in sustainable development</h2>
    <hr class="intro-rule">
    <p class="intro-text">Lorem ipsum dolor sit amet, consectetur adipiscing elit. Pellentesque lobortis accumsan ipsum eu feugiat.<br>Nam vehicula lacus nec magna aliquet a consequat quam tincidunt.</p>
    <a class="btn-primary" href="#">See Our Services</a>
  </section>
</body>
</html>
```